Every Shelf Set Neatly or ESN Organized needs a business card design. ESN Organized is a professi

We need a business card design that is clean, sharp and conveys a sense of organization. I already have a logo.

Target Market(s)

Families (specifically mothers), small business owners, parents, seniors

Industry/Entity Type

Business

Contact Information for Business Card

My website is www.esnorganized-example.com and my Facebook page is http://www.sociallink-example.com/everyshelfsetneatly. The phone number is 418-552-7094 and I want to be listed as Lorna M. Pelham, Owner

Requirements
Must have
• My logo.

```html
<!DOCTYPE html>
<html lang="en">
<head>
<meta charset="utf-8">
<title>ESN Organized – Business Card</title>
<link rel="stylesheet" href="https://fonts.googleapis.com/css2?family=Open+Sans:ital,wght@0,400;0,600;0,700;1,700&display=swap">
<style>
  :root {
    --brand-blue: #0a7bd8;
    --card-white: #ffffff;
    --backdrop: #e9e7e4;
    --ink-white: #ffffff;
  }
  * { margin: 0; padding: 0; box-sizing: border-box; }
  html, body {
    width: 1200px; height: 900px; overflow: hidden;
    background: var(--backdrop);
    font-family: "Open Sans", Arial, sans-serif;
  }
  .stage { position: relative; width: 1200px; height: 900px; }
  .card {
    position: absolute;
    background: var(--card-white);
    overflow: hidden;
    box-shadow: 0 4px 14px rgba(0,0,0,0.15);
  }

  /* Front */
  .card-front { left: 77px; top: 35px; width: 589px; height: 363px; }
  .brand-lockup {
    position: absolute; left: 32px; top: 64px;
    display: flex; align-items: center; gap: 12px;
  }
  .brand-mark {
    width: 22px; height: 22px; background: var(--brand-blue);
  }
  .brand-name {
    color: var(--brand-blue); font-weight: 400;
    font-size: 28px; letter-spacing: 1px; white-space: nowrap;
  }
  .contact-band {
    position: absolute; left: 0; top: 152px; width: 477px; height: 211px;
    background: var(--brand-blue); color: var(--ink-white);
  }
  .person-name { position: absolute; left: 33px; top: 24px; font-size: 21px; font-weight: 700; }
  .person-role { position: absolute; left: 33px; top: 52px; font-size: 14px; }
  .contact-list { position: absolute; left: 33px; top: 98px; list-style: none; }
  .contact-list li {
    display: flex; align-items: center; gap: 8px;
    font-size: 15px; height: 24.5px;
  }
  .contact-list svg { width: 11px; height: 11px; fill: var(--ink-white); flex: none; }

  /* Back */
  .card-back { left: 388px; top: 505px; width: 567px; height: 352px; }
  .name-band {
    position: absolute; left: 0; top: 110px; width: 100%; height: 130px;
    background: var(--brand-blue); color: var(--ink-white);
    display: flex; align-items: center; justify-content: center;
  }
  .band-name { font-size: 30px; font-weight: 400; letter-spacing: 3px; }
  .social-link {
    position: absolute; left: 0; top: 286px; width: 100%; text-align: center;
    color: var(--brand-blue); font-size: 13.5px; font-weight: 700; font-style: italic;
  }
</style>
</head>
<body>
<main class="stage">
  <section class="card card-front" aria-label="Business card front">
    <div class="brand-lockup">
      <span class="brand-mark" aria-hidden="true"></span>
      <span class="brand-name">Every Shelf Set Neatly</span>
    </div>
    <div class="contact-band">
      <p class="person-name">Lorna M. Pelham</p>
      <p class="person-role">Owner</p>
      <ul class="contact-list">
        <li>
          <svg viewBox="0 0 24 24" aria-hidden="true"><path d="M6.6 10.8a15.1 15.1 0 0 0 6.6 6.6l2.2-2.2a1 1 0 0 1 1-.25 11.4 11.4 0 0 0 3.6.57 1 1 0 0 1 1 1V20a1 1 0 0 1-1 1A17 17 0 0 1 3 4a1 1 0 0 1 1-1h3.5a1 1 0 0 1 1 1c0 1.25.2 2.45.57 3.57a1 1 0 0 1-.25 1z"/></svg>
          418-552-7094
        </li>
        <li>
          <svg viewBox="0 0 24 24" aria-hidden="true"><path d="M2 5h20v14H2z M2 5l10 8 10-8" fill="var(--ink-white)"/><path d="M2 6l10 7.5L22 6" fill="none" stroke="var(--brand-blue)" stroke-width="2"/></svg>
          info@esnorganized-example.com
        </li>
        <li>
          <svg viewBox="0 0 24 24" aria-hidden="true"><circle cx="12" cy="12" r="11"/><path d="M1 12h22M12 1c4 4 4 18 0 22M12 1c-4 4-4 18 0 22" fill="none" stroke="var(--brand-blue)" stroke-width="1.6"/></svg>
          www.esnorganized-example.com
        </li>
      </ul>
    </div>
  </section>

  <section class="card card-back" aria-label="Business card back">
    <div class="name-band">
      <p class="band-name">Every Shelf Set Neatly</p>
    </div>
    <p class="social-link">www.sociallink-example.com/everyshelfsetneatly</p>
  </section>
</main>
</body>
</html>
```